Logo and Website Design for QR.KA Horizon - a Software Engineering and IT company

Software engineering and IT are two different disciplines - and yet inseparably linked. At QR.KA Horizon, we combine both worlds and ensure that our software solutions are not only innovative and powerful, but also integrate perfectly into existing IT landscapes. Vision stands more for imagination, so it is not neccessary something what has to do with visualisation. Please consider that the winning competitor is also instructed to make a logo for the company. So please make a suitable logo for QR.KA Horizon to which the website fits to and show it during the website creation process. A good Logo desing is important for winning the competition. The website should contain a landing page with inspiring, perhaps futuristic photos of a datacenter and lines of code. Eventuelly flewent integrated in the text. On the landing page the company should introduced with a small text (max 250 words) followed by a section with a short text to one of our products nearby a graphic visualising the architecture of the product. The menue should be on top and fixed during scrolling and consist of the menue items home, solutions, who are we and a contact button. There should be a footer for linking social media, rights and Impressum. Only as an idea not a must. The very first view on the landing page could also be the menue bar and below of it a transparent unsharp photo (e.g. datacenter, lines of code, both ;) with the company name in the center.

###############################################################

Hi Designers,

Despite your very good approaches for describing QR.KA Horizon, here a short introduction (german text) from ourself:

------
QR.KA Horizon – Ihr Partner für ganzheitliche Softwarelösungen

Die QR.KA Horizon ist ein dynamisches Unternehmen, das sich nicht nur auf die Konzeption, das Design und die Entwicklung maßgeschneiderter Software spezialisiert hat, sondern auch deren reibungslosen Betrieb sicherstellt. Mit einem Team aus erfahrenen Softwarearchitekten und IT-Professionals verbinden wir modernste Softwareentwicklung mit tiefgehendem IT-Know-how – für Lösungen, die nachhaltig, leistungsstark und zukunftssicher sind.

Software Engineering trifft IT – Perfektion in Kombination
Software Engineering und IT sind zwei unterschiedliche Disziplinen – und doch untrennbar miteinander verbunden. Wir bei QR.KA Horizon vereinen beide Welten und sorgen dafür, dass unsere Softwarelösungen nicht nur innovativ und leistungsfähig sind, sondern sich auch perfekt in bestehende IT-Landschaften integrieren.

Expertise mit Fokus auf Healthcare & komplexe IT-Umgebungen
Unsere Experten bringen jahrzehntelange Erfahrung aus dem Healthcare-Sektor mit und unterstützen IT-Abteilungen großer Kliniken in der Entwicklung und Optimierung von Softwarelösungen. Von Anwendungssoftware bis hin zu Steuerungssystemen – unsere Softwareingenieure wissen genau, worauf es ankommt.

Ganzheitlicher Ansatz – über die Software hinaus
Wir entwickeln nicht nur Software, sondern übernehmen auch die Verantwortung für deren stabile und effiziente Betriebsumgebung. Egal, ob on-premises, in der Cloud oder als SaaS-Lösung – wir kümmern uns um den kompletten Lifecycle Ihrer Anwendung.

Ihre Vision – unsere Mission.
Ob Neuentwicklung einer SaaS-Anwendung oder die Migration bestehender Lösungen in eine moderne SaaS-Umgebung – mit QR.KA Horizon haben Sie einen starken Partner an Ihrer Seite.

Lassen Sie uns gemeinsam die Zukunft Ihrer Software gestalten!
--------------

Our first solution called "Clear Record Transfer Gateway" (CLURA)
-------------------
Teilen Sie Ihre Daten sicher – ohne Kompromisse!

Sie nutzen eine relationale Datenbank (Brightcask, Tabulon Hub, Vellumdb etc.) und möchten ausgewählte Daten mit Dritten teilen – sei es für ein Data Warehouse, Business Controller, Lieferanten oder Kunden? Doch dabei sollen Datensicherheit, Integrität und Verfügbarkeit Ihrer primären Lösung in keiner Weise gefährdet werden?

Mit unserer Lösung erhalten Sie genau das: Maximalen Schutz für Ihre Anwendung bei gleichzeitigem Nutzen durch autorisierte Dritte – ganz ohne teure Lizenzkosten für eine Schattendatenbank.

Lassen Sie uns gemeinsam herausfinden, wie Sie Ihre Daten sicher und effizient nutzen können. Kontaktieren Sie uns – wir zeigen Ihnen, was möglich ist!
---------------------

Our second solution MIVO:
---------------------
MIVO – Program for a Tone Matching Instrument ist die smarte Lösung für Unternehmen, die bei Farbgenauigkeit keine Kompromisse machen. Die Software erkennt Farbabweichungen zwischen Mustern vollautomatisch, beschreibt sie verständlich und sorgt so für gleichbleibend hohe Produktqualität – schnell, visuell und präzise. Perfekt für alle, die Farbe zur Vertrauenssache machen.
-------------------------

Thanks,
Gerold

Target Market(s)

IT Professionals from any sector

Industry/Entity Type

Healthcare and other

Coding

Coded - Design and coding required

Number of Pages Required

1 page

Font styles to use
Sans Serif

Colors
0054AA
0677BA
7BADD7
CADEEF
E8F1F8
0094D4
00A9DD
6FCCEA
C7EBF8
E9F6FB
00AB8E
00BBA5
67D7C9
C6EFE9
E9F9F6

Requirements
Must have
• Please see description
Nice to have
• On the landing page the company should introduced with a small text (max 250 words) followed by a section with a short text to one of our products nearby a graphic visualising the architecture of the product. The menue should be on top and fixed during scrolling and consist of the menue items home, solutions, who are we and a contact button. There should be a footer for linking social media, rights and Impressum. Only as an idea not a must. The very first view on the landing page could also be the menue bar and below of it a transparent unsharp photo (e.g. datacenter, lines of code, both ;) with the company name in the center.
Should not have
• Please see description

```html
<!DOCTYPE html>
<html lang="de">
<head>
<meta charset="utf-8">
<title>QR.KA Horizon – Softwarelösungen</title>
<link href="https://fonts.googleapis.com/css2?family=Poppins:wght@400;500;600;700&family=Source+Sans+3:wght@400;600;700&display=swap" rel="stylesheet">
<style>
:root{
  --blue:#0054AA;
  --sky:#C7EBF8;
  --ice:#E8F1F8;
  --teal:#00AB8E;
  --teal-light:#67D7C9;
  --cyan:#6FCCEA;
  --navy:#0C1A4D;
  --navy-bar:#16245A;
  --ink:#111;
  --text:#222;
  --violet:#2A1680;
}
*{margin:0;padding:0;box-sizing:border-box}
html,body{width:1200px;height:3033px;overflow:hidden;background:#fff}
body{position:relative;font-family:"Source Sans 3",sans-serif;color:var(--text)}
.abs{position:absolute}
.btn{position:absolute;display:flex;align-items:center;justify-content:center;border-radius:20px;color:#fff;font-size:14px;font-family:"Source Sans 3",sans-serif}
.btn--blue{background:var(--blue)}
.btn--teal{background:var(--teal)}

/* hero */
.hero-visual{position:absolute;left:0;top:0;width:1200px;height:670px}
.nav{position:absolute;left:141px;top:34px;width:918px;height:57px;background:#fff;border-radius:30px;box-shadow:0 4px 14px rgba(0,0,0,.1);font-family:"Poppins",sans-serif}
.nav__brand{position:absolute;left:32px;top:15px;font-size:21px;font-weight:600;color:var(--navy);letter-spacing:-.2px}
.nav__menu{position:absolute;right:50px;top:19px;display:flex;gap:40px;font-size:13px;color:#222}
.nav__menu span.drop::after{content:"";display:inline-block;margin-left:6px;border:3px solid transparent;border-top:4px solid #333;vertical-align:-1px}
.hero__title{position:absolute;left:151px;top:182px;font-family:"Poppins",sans-serif;font-weight:700;font-size:46px;line-height:58px;color:var(--ink)}
.hero__lead{position:absolute;left:151px;top:374px;font-family:"Poppins",sans-serif;font-size:16px;line-height:30px;color:#111}

/* about */
.about__photo{position:absolute;left:139px;top:766px;width:409px;height:412px;
  background:
    radial-gradient(ellipse 45% 30% at 50% 38%,rgba(90,200,170,.35),transparent 70%),
    radial-gradient(ellipse 60% 30% at 40% 95%,rgba(200,60,110,.45),transparent 70%),
    linear-gradient(160deg,#3b3fc0 0%,#1c1a3a 35%,#241c46 60%,#5a2a6a 85%,#3b3fa0 100%)}
.about__title{position:absolute;left:650px;top:830px;font-weight:700;font-size:28px;line-height:36px;color:var(--ink)}
.about__title .name{color:var(--blue)}
.about__text{position:absolute;left:650px;top:917px;width:410px;font-size:13px;line-height:24px;letter-spacing:.2px;color:#222;text-align:justify}

/* products */
.products{position:absolute;left:0;top:1178px;width:1200px;height:1165px;
  background:
    repeating-linear-gradient(90deg,rgba(255,255,255,.6) 0 1px,transparent 1px 40px),
    repeating-linear-gradient(0deg,rgba(255,255,255,.6) 0 1px,transparent 1px 40px),
    linear-gradient(#fff 0%,var(--ice) 10%,var(--ice) 80%,#fff 100%)}
.products__title{position:absolute;left:0;width:1200px;top:1306px;text-align:center;font-weight:700;font-size:28px;color:var(--ink)}
.products__intro{position:absolute;left:0;width:1200px;top:1357px;text-align:center;font-size:13px;line-height:20px;color:#222}
.product__name{position:absolute;font-weight:600;font-size:16px;line-height:24px;color:var(--ink)}
.product__text{position:absolute;font-size:13px;line-height:23px;color:#222}
.product__visual{position:absolute;width:409px;height:412px;background:var(--violet);overflow:hidden}
.product__visual svg{display:block}

/* cta */
.cta{position:absolute;left:0;top:2397px;width:1200px;height:274px;background:var(--teal-light)}
.cta__title{position:absolute;left:0;width:1200px;top:2462px;text-align:center;font-weight:700;font-size:28px;line-height:42px;color:var(--ink)}

/* footer */
.footer{position:absolute;left:0;top:2671px;width:1200px;height:312px;background:var(--navy)}
.footer__bar{position:absolute;left:0;top:2983px;width:1200px;height:50px;background:var(--navy-bar);color:#fff;font-family:"Poppins",sans-serif;font-size:12px}
.f-brand{position:absolute;left:138px;top:2768px;display:flex;align-items:center;gap:10px;font-family:"Poppins",sans-serif;font-size:22px;font-weight:600;color:#fff}
.f-brand i{width:30px;height:30px;border:2px solid #fff;border-radius:50%}
.f-tag{position:absolute;left:141px;top:2816px;font-family:"Poppins",sans-serif;font-size:13px;line-height:23px;color:#fff}
.f-social{position:absolute;left:140px;top:2892px;display:flex;gap:26px}
.f-social span{width:18px;height:18px;border-radius:50%;border:2px solid #fff}
.f-head{position:absolute;font-family:"Poppins",sans-serif;font-weight:600;font-size:16px;color:#fff}
.f-head::after{content:"";position:absolute;left:0;top:30px;width:24px;height:3px;background:#2fb5e8}
.f-links{position:absolute;left:436px;top:2814px;font-family:"Poppins",sans-serif;font-size:13px;line-height:28.5px;color:#fff;list-style:none}
.f-links li::before{content:"";display:inline-block;margin-right:10px;border:4px solid transparent;border-left:5px solid #2fb5e8;border-right:0}
.f-contact{position:absolute;left:616px;display:flex;align-items:center;gap:14px;font-family:"Poppins",sans-serif;font-size:13px;color:#fff}
.f-contact .ico{width:32px;height:32px;border-radius:50%;background:#25356a;display:flex;align-items:center;justify-content:center}
.f-input{position:absolute;left:861px;top:2817px;width:198px;height:38px;border:1px solid #7b88b0;border-radius:20px;font-family:"Poppins",sans-serif;font-size:11px;color:#aab;padding:11px 21px}
.f-submit{position:absolute;left:861px;top:2875px;width:198px;height:38px;border-radius:20px;background:#0a7fe0;color:#fff;font-family:"Poppins",sans-serif;font-weight:600;font-size:13px;display:flex;align-items:center;justify-content:center}
</style>
</head>
<body>

<svg class="hero-visual" viewBox="0 0 1200 670">
  <defs>
    <linearGradient id="dataBase" x1="0" y1="0" x2="1" y2="1">
      <stop offset="0" stop-color="#1a1410"/>
      <stop offset=".35" stop-color="#3a1f12"/>
      <stop offset=".6" stop-color="#0b2540"/>
      <stop offset="1" stop-color="#081a2e"/>
    </linearGradient>
    <radialGradient id="warmGlow" cx=".38" cy=".45" r=".4">
      <stop offset="0" stop-color="#e0782a" stop-opacity=".85"/>
      <stop offset="1" stop-color="#e0782a" stop-opacity="0"/>
    </radialGradient>
    <radialGradient id="coolGlow" cx=".8" cy=".5" r=".45">
      <stop offset="0" stop-color="#3aa6e0" stop-opacity=".75"/>
      <stop offset="1" stop-color="#3aa6e0" stop-opacity="0"/>
    </radialGradient>
    <clipPath id="heroClip">
      <path d="M735 70 C660 160 620 200 528 300 C515 380 530 470 605 505 C700 540 800 460 900 460 C1000 460 1090 462 1200 470 L1200 0 L748 0 Z"/>
    </clipPath>
  </defs>
  <path d="M725 70 C640 160 610 190 520 300 C500 380 520 480 600 515 C700 550 800 470 900 470 C1000 470 1090 470 1200 480 L1200 0 L742 0 Z" fill="var(--sky)"/>
  <path d="M1040 470 C1110 490 1140 590 1200 662 L1200 600 C1160 560 1130 480 1080 470 Z" fill="var(--sky)"/>
  <g clip-path="url(#heroClip)" role="img" aria-label="Photo: glowing server racks with lines of code in orange and blue light">
    <rect x="500" y="0" width="700" height="560" fill="url(#dataBase)"/>
    <rect x="500" y="0" width="700" height="560" fill="url(#warmGlow)"/>
    <rect x="500" y="0" width="700" height="560" fill="url(#coolGlow)"/>
  </g>
</svg>

<nav class="nav">
  <div class="nav__brand">QR.KA HORIZON</div>
  <div class="nav__menu">
    <span>Heim</span>
    <span class="drop">Lösungen</span>
    <span class="drop">Wer Sind Wir</span>
  </div>
</nav>

<h1 class="hero__title">Mit Präzision<br>Die Zukunft<br>Voramtreiben</h1>
<p class="hero__lead">Innovative Lösungen für Leistung,<br>Sicherheit und Skalierbarkeit</p>
<a class="btn btn--blue" style="left:151px;top:451px;width:155px;height:34px">Legen Sie los</a>

<div class="about__photo" role="img" aria-label="Photo: developer workstation with monitors full of code at night"></div>
<h2 class="about__title"><span class="name">QR.KA Horizon</span>-Ihr Partner für<br>ganzheitliche Softwarelösungen</h2>
<p class="about__text">QR.KA Horizon ist ein dynamisches Unternehmen, das sich nicht nur auf die Konzeption, Gestaltung und Entwicklung von Individualsoftware spezialisiert hat, sondern auch für deren reibungslosen Betrieb sorgt. Mit einem Team aus erfahrenen Softwarearchitekten und IT-Profis verbinden wir modernste Softwareentwicklung mit fundiertem IT-Know-how - für Lösungen, die nachhaltig, leistungsstark und zukunftssicher sind.</p>

<section class="products"></section>
<h2 class="products__title">Ausgewähltes Produkt</h2>
<p class="products__intro">Lorem ipsum dolor sit amet, consectetuer adipiscing elit, sed diam nonummy nibh euismod<br>tincidunt ut laoreet dolore magna aliquam erat volutpat wisi enim ad minim veniam</p>

<h3 class="product__name" style="left:141px;top:1466px">Klare Datensatz-Übertragungsschnittstelle (CLURA)</h3>
<p class="product__text" style="left:141px;top:1500px;width:415px">Sie verwenden eine relationale Datenbank (Brightcask, Tabulon Hub, Vellumdb usw.) und möchten ausgewählte Daten mit Dritten teilen - sei es für ein Data Warehouse, Business Controller, Lieferanten oder Kunden? Sie wollen aber die Datensicherheit, -integrität und -verfügbarkeit Ihrer primären Lösung in keiner Weise gefährden? Mit unserer Lösung erhalten Sie genau das: maximalen Schutz für Ihre Anwendung bei gleichzeitiger Nutzung durch autorisierte Dritte - ohne die teuren Lizenzkosten für eine Schattendatenbank.<br>Lassen Sie uns gemeinsam herausfinden, wie Sie Ihre Daten sicher und effizient nutzen können.</p>
<a class="btn btn--teal" style="left:141px;top:1754px;width:156px;height:34px">Kontaktieren Sie uns</a>

<div class="product__visual" style="left:651px;top:1438px">
  <svg width="409" height="412" viewBox="0 0 409 412" role="img" aria-label="Architekturdiagramm: Primärdatenbank über ein gesichertes Gateway mit mehreren Empfängern verbunden">
    <defs>
      <marker id="arrowHead" viewBox="0 0 10 10" refX="9" refY="5" markerWidth="7" markerHeight="7" orient="auto">
        <path d="M0 0 L10 5 L0 10 Z" fill="var(--cyan)"/>
      </marker>
    </defs>
    <circle cx="204" cy="206" r="178" fill="#34209a"/>
    <!-- primary database -->
    <rect x="38" y="156" width="82" height="100" rx="10" fill="#4a34c4" stroke="var(--cyan)" stroke-width="2"/>
    <ellipse cx="79" cy="184" rx="26" ry="8" fill="none" stroke="var(--cyan)" stroke-width="2"/>
    <path d="M53 184 V226 A26 8 0 0 0 105 226 V184" fill="none" stroke="var(--cyan)" stroke-width="2"/>
    <path d="M53 205 A26 8 0 0 0 105 205" fill="none" stroke="var(--cyan)" stroke-width="2"/>
    <!-- gateway -->
    <rect x="164" y="166" width="82" height="80" rx="10" fill="var(--teal)" stroke="#C6EFE9" stroke-width="2"/>
    <rect x="188" y="196" width="34" height="28" rx="4" fill="none" stroke="#fff" stroke-width="2.5"/>
    <path d="M194 196 V188 A11 11 0 0 1 216 188 V196" fill="none" stroke="#fff" stroke-width="2.5"/>
    <!-- receivers -->
    <rect x="292" y="84" width="80" height="58" rx="8" fill="#4a34c4" stroke="var(--cyan)" stroke-width="2"/>
    <rect x="292" y="177" width="80" height="58" rx="8" fill="#4a34c4" stroke="var(--cyan)" stroke-width="2"/>
    <rect x="292" y="270" width="80" height="58" rx="8" fill="#4a34c4" stroke="var(--cyan)" stroke-width="2"/>
    <g fill="var(--cyan)">
      <rect x="306" y="120" width="8" height="12"/><rect x="319" y="110" width="8" height="22"/><rect x="332" y="102" width="8" height="30"/><rect x="345" y="114" width="8" height="18"/>
      <rect x="306" y="193" width="52" height="5" rx="2"/><rect x="306" y="204" width="40" height="5" rx="2"/><rect x="306" y="215" width="46" height="5" rx="2"/>
      <circle cx="332" cy="292" r="9"/><rect x="316" y="305" width="32" height="12" rx="6"/>
    </g>
    <!-- connectors -->
    <path d="M122 206 H160" stroke="var(--cyan)" stroke-width="3" fill="none" marker-end="url(#arrowHead)"/>
    <path d="M248 190 C270 170 270 113 288 113" stroke="var(--cyan)" stroke-width="3" fill="none" marker-end="url(#arrowHead)"/>
    <path d="M248 206 H288" stroke="var(--cyan)" stroke-width="3" fill="none" marker-end="url(#arrowHead)"/>
    <path d="M248 222 C270 242 270 299 288 299" stroke="var(--cyan)" stroke-width="3" fill="none" marker-end="url(#arrowHead)"/>
    <path d="M79 262 V330 H204 V252" stroke="#67D7C9" stroke-width="2" stroke-dasharray="5 6" fill="none"/>
  </svg>
</div>

<div class="product__visual" style="left:145px;top:1889px" role="img" aria-label="Illustration: laptop with magnifier inspecting colour samples">
  <svg width="409" height="412" viewBox="0 0 409 412" aria-hidden="true">
    <circle cx="204" cy="206" r="178" fill="#34209a"/>
  </svg>
</div>
<h3 class="product__name" style="left:650px;top:1965px">Programm zum Farbtonabgleich<br>(MIVO)</h3>
<p class="product__text" style="left:650px;top:2025px;width:410px">MIVO ist die intelligente Lösung für Unternehmen, die bei der Farbgenauigkeit keine Kompromisse eingehen. Die Software erkennt automatisch Farbabweichungen zwischen Mustern, beschreibt sie eindeutig und sorgt so für eine gleichbleibend hohe Produktqualität - schnell, visuell und präzise. Perfekt für alle, die Farbe zur Vertrauenssache machen.</p>
<a class="btn btn--teal" style="left:650px;top:2187px;width:156px;height:34px">Kontaktieren Sie uns</a>

<section class="cta"></section>
<h2 class="cta__title">Ermutigung der Besucher, sich mit Ihnen in Verbindung zu setzen, um<br>Lösungen für die sichere und effiziente Nutzung ihrer Daten zu finden.</h2>
<a class="btn btn--blue" style="left:523px;top:2564px;width:155px;height:34px">Kontaktieren Sie uns</a>

<footer class="footer"></footer>
<div class="f-brand"><i></i>QR.KA HORIZON</div>
<p class="f-tag">Innovative Software trifft auf<br>echte IT-Expertise</p>
<div class="f-social">
  <span aria-label="Soziales Netzwerk 1"></span>
  <span aria-label="Soziales Netzwerk 2"></span>
  <span aria-label="Soziales Netzwerk 3"></span>
  <span aria-label="Soziales Netzwerk 4"></span>
</div>

<div class="f-head" style="left:436px;top:2763px">Quicklinks</div>
<ul class="f-links"><li>Heim</li><li>Lösungen</li><li>Wer Sind Wir</li><li>Kontakt</li></ul>

<div class="f-head" style="left:616px;top:2763px">Kontakt Uns</div>
<div class="f-contact" style="top:2808px">
  <span class="ico"><svg width="14" height="14" viewBox="0 0 24 24"><path fill="#fff" d="M6.6 10.8a15.1 15.1 0 006.6 6.6l2.2-2.2c.3-.3.7-.4 1-.2 1.1.4 2.3.6 3.6.6.6 0 1 .4 1 1V20c0 .6-.4 1-1 1A17 17 0 013 4c0-.6.4-1 1-1h3.5c.6 0 1 .4 1 1 0 1.3.2 2.5.6 3.6.1.3 0 .7-.2 1z"/></svg></span>
  (555)-014-2290
</div>
<div class="f-contact" style="top:2853px">
  <span class="ico"><svg width="14" height="12" viewBox="0 0 24 18"><rect x="1" y="1" width="22" height="16" rx="2" fill="none" stroke="#fff" stroke-width="2"/><path d="M1 2l11 8 11-8" fill="none" stroke="#fff" stroke-width="2"/></svg></span>
  info@qrka-horizon.example
</div>

<div class="f-head" style="left:861px;top:2760px">Newsletter Abonnieren</div>
<div class="f-input">Eingeben E-Mail</div>
<div class="f-submit">Jetzt Abonnieren</div>

<div class="footer__bar">
  <span class="abs" style="left:141px;top:17px">Copyright © 2025 QR.KA Horizon Software Engineering | Alle Rechte Vorbehalten.</span>
  <span class="abs" style="left:990px;top:17px">Impressum</span>
</div>

</body>
</html>
```